Quote Cards With KB May 2025 for Instagram

I would like to put these quotes over one of the pictures attached; Instagram (new size: 4:5 (1080 x 1350 pixels) One Quote per picture, and I want the quote to be bold or easy to read as well. I provided a few reference graphics that I really like as examples below. In very small letters at the bottom add @KBHarlowOnline

All of the pictures are attached; you can pick any photo and add one quote to it; but no stock photography

```html
<!DOCTYPE html>
<html lang="en">
<head>
<meta charset="utf-8">
<title>Quote Cards With KB – May 2025</title>
<link rel="stylesheet" href="https://fonts.googleapis.com/css2?family=Playfair+Display:wght@700;800;900&family=Roboto+Slab:wght@500;600&family=Poppins:wght@400;500;600;700&family=Cormorant+Garamond:wght@500&display=swap">
<style>
  :root {
    --page: #ffffff;
    --ink: #2b2b2b;
    --pink-deep: #c8176f;
    --pink-bright: #f0529c;
    --panel-dark: #3d3d3d;
    --panel-light: rgba(246, 246, 246, 0.92);
    --shadow: 0 2px 10px rgba(0, 0, 0, 0.08);
  }
  * { margin: 0; padding: 0; box-sizing: border-box; }
  html, body { width: 1200px; height: 1200px; overflow: hidden; background: var(--page); }
  .board { position: relative; width: 1200px; height: 1200px; }

  .card {
    position: absolute; width: 418px; height: 523px;
    overflow: hidden; background: #fff; box-shadow: var(--shadow);
  }
  .card--tl { left: 169px; top: 60px; }
  .card--tr { left: 620px; top: 60px; }
  .card--bl { left: 169px; top: 624px; }
  .card--br { left: 620px; top: 624px; }

  .photo { position: absolute; }
  .line { position: absolute; line-height: 1; white-space: nowrap; }
  .center { left: 195px; width: 223px; text-align: center; }
  .slab { font-family: "Roboto Slab", serif; font-weight: 600; color: var(--ink); transform-origin: left top; }
  .display { font-family: "Playfair Display", serif; font-weight: 900; letter-spacing: -1px; }
  .sans { font-family: "Poppins", sans-serif; }
  .deep { color: var(--pink-deep); }
  .bright { color: var(--pink-bright); }
  .handle {
    position: absolute; font-family: "Cormorant Garamond", serif; font-weight: 500;
    font-size: 13px; letter-spacing: 1.6px; color: var(--ink); line-height: 1;
  }

  /* Card 1 */
  .card--tl .photo { inset: 0; background: linear-gradient(160deg, #d9d6da 0%, #cdb7c0 40%, #b9939f 70%, #9c8a6a 100%); }
  .card--tl .panel { position: absolute; left: 195px; top: 0; width: 223px; height: 100%; background: var(--panel-light); }
  .card--tl .center.slab { transform: scaleX(0.8); transform-origin: center top; }

  /* Card 2 */
  .card--tr .photo { inset: 0; background: linear-gradient(90deg, #ffffff 35%, #efe3ee 55%, #d58ec6 72%, #b98fd0 88%, #e9e2f2 100%); }

  /* Card 3 */
  .card--bl .photo { left: 0; top: 0; width: 185px; height: 100%; background: linear-gradient(180deg, #eef2f3 0%, #b7b9b4 40%, #3a3a3a 65%, #1f1f1f 100%); }
  .card--bl .panel { position: absolute; left: 185px; top: 0; width: 233px; height: 100%; background: var(--panel-dark); }
  .card--bl .line.sans { color: #fff; font-weight: 600; }
  .card--bl .slab { color: #fff; }
  .card--bl .handle { color: #fff; }

  /* Card 4 */
  .card--br .photo { inset: 0; background: linear-gradient(115deg, #ffffff 42%, #e6e6e6 58%, #5a5a5a 78%, #2a2a2a 100%); }
</style>
</head>
<body>
<main class="board">

  <article class="card card--tl">
    <div class="photo" role="img" aria-label="KB in a blush rhinestone bodysuit beside sunflowers and glass panels"></div>
    <div class="panel"></div>
    <div class="line slab center" style="top:32px;font-size:33px;">FLAT TUMMY</div>
    <div class="line slab center" style="top:70px;font-size:33px;">IN YOUR 40S?</div>
    <div class="line display deep center" style="top:190px;font-size:38px;">IT’S STILL</div>
    <div class="line display deep center" style="top:230px;font-size:38px;">POSSIBLE!</div>
    <div class="line sans center" style="top:341px;font-size:14px;color:var(--ink);">COMMENT</div>
    <div class="line sans deep center" style="top:358px;font-size:26px;font-weight:700;">BYE BELLY</div>
    <div class="line sans center" style="top:388px;font-size:14px;color:var(--ink);">to get the 10 secrets</div>
    <div class="line sans center" style="top:405px;font-size:14px;color:var(--ink);">to a flatter tummy</div>
    <div class="handle center" style="top:491px;">@KBHARLOWONLINE</div>
  </article>

  <article class="card card--tr">
    <div class="photo" role="img" aria-label="KB in a fuchsia gown on a lit stage"></div>
    <div class="line sans" style="left:30px;top:35px;font-size:25px;font-weight:600;color:var(--ink);">Bloating.</div>
    <div class="line sans" style="left:30px;top:64px;font-size:25px;font-weight:600;color:var(--ink);">Muffin top.</div>
    <div class="line sans" style="left:30px;top:93px;font-size:25px;font-weight:600;color:var(--ink);">Puffy waistline.</div>
    <div class="line display deep" style="left:33px;top:204px;font-size:37px;">YOUR BODY’S</div>
    <div class="line display deep" style="left:33px;top:238px;font-size:37px;">SCREAMING</div>
    <div class="line slab" style="left:34px;top:281px;font-size:21px;transform:scaleX(0.8);">for a different kind of fix.</div>
    <div class="line display bright" style="left:35px;top:370px;font-size:35px;letter-spacing:2px;font-weight:800;">HERE IT IS</div>
    <div class="handle" style="left:49px;top:484px;">@KBHARLOWONLINE</div>
  </article>

  <article class="card card--bl">
    <div class="photo" role="img" aria-label="KB in a black outfit on a hillside overlook"></div>
    <div class="panel"></div>
    <div class="line sans" style="left:199px;top:93px;font-size:20px;">You’re doing all the</div>
    <div class="line sans" style="left:218px;top:117px;font-size:20px;"><span class="display deep" style="font-size:27px;">“RIGHT”</span> things,</div>
    <div class="line sans" style="left:203px;top:202px;font-size:20px;">but your belly</div>
    <div class="line sans" style="left:213px;top:226px;font-size:20px;"><span class="display deep" style="font-size:27px;">WON’T</span> go down?</div>
    <div class="line slab center" style="left:185px;width:233px;top:326px;font-size:26px;transform:scaleX(0.85);transform-origin:center top;">Here’s what</div>
    <div class="line display bright center" style="left:185px;width:233px;top:353px;font-size:31px;">YOU HAVEN’T</div>
    <div class="line display bright center" style="left:185px;width:233px;top:381px;font-size:43px;">TRIED</div>
    <div class="handle center" style="left:185px;width:233px;top:485px;">@KBHARLOWONLINE</div>
  </article>

  <article class="card card--br">
    <div class="photo" role="img" aria-label="KB dancing in a sheer black striped top indoors"></div>
    <div class="line slab" style="left:27px;top:30px;font-size:22px;transform:scaleX(0.82);">This 90-day plan helped</div>
    <div class="line display deep" style="left:27px;top:57px;font-size:37px;">WOMEN OVER 40</div>
    <div class="line display bright" style="left:27px;top:91px;font-size:44px;">SLIM DOWN,</div>
    <div class="line sans" style="left:27px;top:158px;font-size:19px;color:var(--ink);">get a tiny waist and</div>
    <div class="line slab" style="left:26px;top:185px;font-size:34px;transform:scaleX(0.78);">feel sexy again</div>
    <div class="line display bright" style="left:27px;top:346px;font-size:34px;">YOU’RE NEXT</div>
    <div class="handle" style="left:28px;top:485px;">@KBHARLOWONLINE</div>
  </article>

</main>
</body>
</html>
```